Torvane Halbridge

Looking for modern business cards.
Clean contemporary design.
Similar to this.
https://www.plumvexa-search.example/imgres?imgurl=https%3A%2F%2Fimg.quorlint-cdn.example%2Fsleek_dark_metal_card_design_540.jpg&imgrefurl=https%3A%2F%2Fwww.quorlint-prints.example%2Fsleek_dark_metal_card_design-918273645501928374&q=modern%20business%20cards

But I'd like the blue to look metallic.

Business

```html
<!DOCTYPE html>
<html lang="en">
<head>
<meta charset="utf-8">
<title>Torvane Halbridge – Business Card</title>
<link rel="stylesheet" href="https://fonts.googleapis.com/css2?family=Roboto:ital,wght@0,400;0,700;1,700&family=Roboto+Condensed:wght@700&display=swap">
<style>
  :root {
    --backdrop: #e2e2e2;
    --paper: #f4f4f4;
    --navy: #24516b;
    --teal: #2a9fc0;
    --ink: #4d4d4d;
    --rule: #8a8a8a;
    --steel-1: #3c81a3;
    --steel-2: #5a9dbd;
    --steel-3: #4a8db0;
    --white: #ffffff;
  }
  * { margin: 0; padding: 0; box-sizing: border-box; }
  html, body { width: 1200px; height: 960px; overflow: hidden; }
  body {
    position: relative;
    background: var(--backdrop);
    font-family: "Roboto", Arial, sans-serif;
  }
  .card {
    position: absolute;
    width: 602px;
    height: 343px;
    box-shadow: 2px 3px 4px rgba(0,0,0,0.35);
  }
  .card-front { left: 314px; top: 113px; background: var(--paper); }
  .card-back {
    left: 311px; top: 472px; width: 600px;
    background:
      repeating-linear-gradient(0deg, rgba(255,255,255,0.05) 0 1px, rgba(0,0,0,0.04) 1px 3px),
      linear-gradient(100deg, var(--steel-1) 0%, var(--steel-2) 28%, var(--steel-3) 50%, var(--steel-2) 72%, var(--steel-1) 100%);
  }
  .brand {
    position: absolute;
    display: flex;
    align-items: center;
    gap: 8px;
    font-family: "Roboto", Arial, sans-serif;
    font-weight: 700;
    white-space: nowrap;
  }
  .brand-dot { border-radius: 50%; flex: none; }
  .card-front .brand { right: 92px; top: 76px; font-size: 25px; color: var(--navy); }
  .card-front .brand-dot { width: 14px; height: 14px; background: var(--teal); }
  .tagline {
    position: absolute;
    font-style: italic;
    font-weight: 700;
    white-space: nowrap;
  }
  .card-front .tagline { right: 80px; top: 106px; font-size: 6.5px; letter-spacing: 0.6px; color: var(--teal); }
  .accent-bar { position: absolute; left: 0; top: 150px; width: 16px; height: 41px; background: var(--teal); }
  .person-name {
    position: absolute; left: 39px; top: 147px;
    font-family: "Roboto Condensed", "Arial Narrow", sans-serif;
    font-weight: 700; font-size: 22px; color: var(--navy);
  }
  .person-title {
    position: absolute; left: 39px; top: 175px;
    font-size: 14px; font-weight: 400; color: var(--teal);
  }
  .contact-list { position: absolute; left: 39px; top: 217px; list-style: none; }
  .contact-list li {
    display: flex; align-items: center; gap: 8px;
    height: 19px; font-size: 14.5px; color: var(--ink);
  }
  .contact-list svg { width: 14px; height: 14px; fill: var(--navy); flex: none; }
  .divider { position: absolute; left: 234px; top: 278px; width: 1px; height: 31px; background: var(--rule); }
  .address { position: absolute; left: 256px; top: 274px; font-size: 14.5px; line-height: 19px; color: var(--ink); font-style: normal; }
  .card-back .brand { left: 101px; top: 156px; font-size: 40px; color: var(--white); gap: 12px; }
  .card-back .brand-dot { width: 20px; height: 20px; background: var(--white); }
  .card-back .tagline { left: 194px; top: 207px; font-size: 9px; letter-spacing: 1px; color: var(--white); }
</style>
</head>
<body>

<section class="card card-front">
  <div class="brand"><span class="brand-name">Torvane Halbridge</span><span class="brand-dot"></span></div>
  <p class="tagline">“Helping bright ideas grow into strong firms”</p>

  <div class="accent-bar"></div>
  <h1 class="person-name">ELSA MARROW</h1>
  <p class="person-title">CEO/FOUNDER</p>

  <ul class="contact-list">
    <li><svg viewBox="0 0 24 24" aria-hidden="true"><path d="M6.6 10.8a15.5 15.5 0 0 0 6.6 6.6l2.2-2.2c.3-.3.7-.4 1-.2 1.1.4 2.3.6 3.6.6.6 0 1 .4 1 1V20c0 .6-.4 1-1 1A17 17 0 0 1 3 4c0-.6.4-1 1-1h3.5c.6 0 1 .4 1 1 0 1.3.2 2.5.6 3.6.1.3 0 .7-.2 1z"/></svg>555 214 0387</li>
    <li><svg viewBox="0 0 24 24" aria-hidden="true"><path d="M7 1h10a2 2 0 0 1 2 2v18a2 2 0 0 1-2 2H7a2 2 0 0 1-2-2V3a2 2 0 0 1 2-2zm0 3v14h10V4zm5 15.5a1.2 1.2 0 1 0 0 2.4 1.2 1.2 0 0 0 0-2.4z"/></svg>555 730 4129</li>
    <li><svg viewBox="0 0 24 24" aria-hidden="true"><path d="M6 2h10l2 2v5H6zM3 10h18a2 2 0 0 1 2 2v6h-4v4H5v-4H1v-6a2 2 0 0 1 2-2zm4 6v4h10v-4z"/></svg>555 618 2256</li>
    <li><svg viewBox="0 0 24 24" aria-hidden="true"><path d="M2 5h20v14H2zm2 2v.4l8 5 8-5V7l-8 5z"/></svg>elsa@torvane.example</li>
    <li><svg viewBox="0 0 24 24" aria-hidden="true"><path d="M12 2a10 10 0 1 0 0 20 10 10 0 0 0 0-20zm-1 17.9A8 8 0 0 1 4.2 10L9 14.8v1a2 2 0 0 0 2 2zm6.9-2.5a2 2 0 0 0-1.9-1.4h-1v-3a1 1 0 0 0-1-1H8v-2h2a1 1 0 0 0 1-1V7h2a2 2 0 0 0 2-2v-.4a8 8 0 0 1 2.9 12.8z"/></svg>www.torvane.example</li>
  </ul>
  <div class="divider"></div>
  <address class="address">4120 Alder Crest Way<br>Brookhaven, Vermont 05921</address>
</section>

<section class="card card-back">
  <div class="brand"><span class="brand-name">Torvane Halbridge</span><span class="brand-dot"></span></div>
  <p class="tagline">“Helping Bright Ideas Grow into Strong Firms”</p>
</section>

</body>
</html>
```